Home Page Design (+50 More Pages To Winning Designer!)

We have a 50+ page website, but we're starting with the home page. The winning designer will get all 50+ pages to design as a 2nd project, so make sure you do your best!

Velorane is in the private jet industry and needs a re-designed website.

We have created the structure for the website and content inside of Frandle.io (THESE ARE ONLY ROUGH A.I. GENERATED WIREFRAMES AND DO NOT NEED TO BE FOLLOWED EXACTLY) - https://www.frandle.io/app/project/K482915_qWmRtZaLs-KDnHoUvvy82QJ5cfhaR61trkwqlDV3Hm

Take the content from the 'Home Page' under the 'Wireframe' tab on the Frandle.io link above, but feel free to re-design the page in a better way as these are only A.I. generated wireframes.

We want a DARK theme.... High quality, luxurious feel, greyscale colors. Attached is a brand guideline (BUT THIS IS NOT A 100% BRAND GUIDELINE, YOU CAN CHANGE COLORS AND FONTS AND MAKE CHANGES IF YOU HAVE BETTER IDEAS) and attached is our logo. We are also attaching some examples of other apps and websites to give you a guideline of what we're looking for for this design project.

The final design MUST communicate luxury using high-quality imagery of large cabin luxurious private jets.
Updates

ENTRIES THAT DO NOT FOLLOW THE PROJECT BRIEF WILL BE AUTOMATICALLY DISCARDED. FOLLOW THE INSTRUCTIONS!

Industry/Entity Type

Travel

Number of Pages Required

1 page

Font styles to use
Sans Serif

Colors

Designer to choose colors to be used in the design.

Requirements
Must have
• Follow wireframe and use content in wireframe (see Frandle.io link)

```html
<!DOCTYPE html>
<html lang="en">
<head>
<meta charset="utf-8">
<title>Velorane — Luxury in the Skies</title>
<link href="https://fonts.googleapis.com/css2?family=Montserrat:ital,wght@0,400;0,500;0,600;0,700;1,400&display=swap" rel="stylesheet">
<style>
:root{
  --bg:#0c0c0d;
  --surface:#141415;
  --card:#1c1c1e;
  --accent:#3b3b3f;
  --accent-soft:#2a2a2d;
  --line:#4a4a4f;
  --white:#fff;
  --text:#ececee;
  --muted:#a4a4aa;
  --dim:#77777d;
}
*{box-sizing:border-box;margin:0;padding:0}
html,body{width:1200px;height:2997px;overflow:hidden;background:var(--bg)}
body{position:relative;font-family:'Montserrat',sans-serif;color:var(--text)}
.abs{position:absolute}
.site-header .logo{left:0;width:1200px;top:14px;text-align:center;font-size:20px;font-weight:500;letter-spacing:-.3px;color:var(--white)}
.nav{left:215px;width:750px;display:flex;justify-content:space-between;font-size:11px;font-weight:600;color:var(--text)}
.header-nav{top:56px}
.hero{left:0;top:79px;width:1200px;height:451px;background:linear-gradient(180deg,#2c2c30 0%,#5a5a60 30%,#7a7a80 50%,#3a3a3e 75%,#121213 100%)}
.hero .shade{left:0;top:0;width:1200px;height:451px;background:linear-gradient(90deg,rgba(0,0,0,.6),rgba(0,0,0,0) 60%)}
.hero h1{left:215px;top:218px;font-size:33px;font-weight:600;color:var(--white);letter-spacing:.3px}
.hero p{left:215px;top:270px;width:405px;font-size:12px;line-height:18px;color:var(--white)}
.btn{display:flex;align-items:center;justify-content:center;font-size:8.5px;font-weight:700;letter-spacing:1.3px;text-transform:uppercase}
.btn-accent{background:var(--accent);color:var(--white)}
.btn-white{background:var(--white);color:#000}
.hero .btn{left:215px;top:356px;width:132px;height:32px}
.intro-title{left:0;width:1200px;top:553px;text-align:center;font-size:19.5px;font-weight:600;color:var(--white)}
.intro-sub{left:0;width:1200px;top:586px;text-align:center;font-size:13px;color:var(--text)}
.chevron{left:574px;top:626px}
.feature{width:172px;height:160px;top:724px;background:var(--card);color:var(--white);border:1px solid #2c2c30}
.feature svg{position:absolute;left:20px;top:16px}
.feature p{position:absolute;left:18px;top:61px;width:140px;font-size:9px;line-height:15px;color:var(--text)}
.feature .label{position:absolute;left:-1px;bottom:-1px;width:172px;height:30px;background:var(--accent);font-size:8.5px;font-weight:600;letter-spacing:1.3px;text-transform:uppercase;display:flex;align-items:center;justify-content:center;clip-path:polygon(0 0,100% 0,100% 70%,94% 100%,0 100%)}
.redefine-photo{left:600px;top:910px;width:600px;height:379px;background:radial-gradient(circle at 55% 35%,#f2f2f2 0%,#b8b8bb 25%,#6c6c70 60%,#3a3a3d 100%)}
.redefine h2{left:215px;top:986px;font-size:22px;font-weight:500;color:var(--white)}
.redefine p{left:215px;top:1030px;width:335px;font-size:11.5px;line-height:23.5px;color:var(--text)}
.redefine .btn{left:215px;top:1139px;width:154px;height:32px}
.journey{left:0;top:1334px;width:1200px;height:448px;background:linear-gradient(180deg,#161618 0%,#232326 40%,#3a3a3e 70%,#4a4a4f 85%,#2a2a2d 100%)}
.journey h2{left:214px;top:32px;font-size:22px;font-weight:600;color:var(--white)}
.journey .tagline{left:215px;top:62px;font-size:13px;font-weight:500;color:var(--white)}
.journey p{left:215px;top:96px;width:460px;font-size:11.5px;line-height:19px;color:var(--white)}
.service{top:264px;width:160px;text-align:center;color:var(--white);font-size:7px;font-weight:700;letter-spacing:1.2px}
.service svg{display:block;margin:0 auto 6px}
.journey .cta{left:0;width:1200px;top:336px;text-align:center;font-size:12.5px;color:var(--white)}
.journey .btn{left:539px;top:376px;width:123px;height:32px}
.clients h2{left:215px;top:1840px;font-size:22px;font-weight:700;color:var(--white)}
.clients .lead{left:215px;top:1876px;width:520px;font-size:16px;font-weight:600;line-height:32.5px;color:var(--text)}
.clients .btn{left:215px;top:2004px;width:124px;height:31px}
.world-map{left:81px;top:1909px;width:1025px;height:535px;background:radial-gradient(ellipse at 50% 50%,rgba(120,120,128,.35) 0%,rgba(90,90,96,.18) 55%,rgba(12,12,13,0) 75%)}
.bubble path{fill:var(--accent-soft)}
.bubble .ring{fill:var(--white)}
.bubble .ring-in{fill:var(--accent-soft)}
.quote-text{left:650px;top:2022px;width:280px;font-size:13.5px;font-style:italic;line-height:18px;color:var(--white)}
.partners{top:2493px;font-size:26px;font-weight:600;color:var(--muted);letter-spacing:2px}
.footer{left:0;top:2559px;width:1200px;height:438px;background:var(--surface);border-top:1px solid #2a2a2d;color:var(--white)}
.footer .logo{left:215px;top:37px;font-size:19px;font-weight:500;display:flex;align-items:center;gap:6px}
.footer .logo span.mark{width:12px;height:12px;background:var(--white);display:inline-block}
.footer .tag{left:215px;top:68px;width:300px;font-size:10px;line-height:16px;color:var(--text)}
.footer .nav{top:126px}
.footer .rule{left:215px;top:146px;width:750px;height:1px;background:var(--line)}
.footer h3{left:215px;top:190px;font-size:18px;font-weight:400;letter-spacing:.3px}
.contact{left:215px;font-size:11px;line-height:18px;display:flex;gap:10px;align-items:flex-start;color:var(--text)}
.contact svg{margin-top:3px;flex:none}
.social{top:2753px;width:14px;height:14px;border-radius:50%;background:var(--white)}
.newsletter{left:705px;top:2800px;width:270px;font-size:10.5px;line-height:17px;color:var(--text)}
.email-input{left:705px;top:2860px;width:156px;border-bottom:1.5px solid var(--white);font-size:10px;font-style:italic;color:var(--muted);padding-bottom:3px}
.subscribe{left:873px;top:2853px;width:91px;height:28px;background:var(--white);color:#000;display:flex;align-items:center;justify-content:center;font-size:8px;font-weight:700;letter-spacing:.8px}
.legal{top:2966px;font-size:10.5px;color:var(--text)}
</style>
</head>
<body>

<header class="site-header">
  <div class="abs logo">Velorane</div>
  <nav class="abs nav header-nav">
    <span>Aircraft</span><span>Programs</span><span>Why velorane</span><span>Lifestyle</span><span>Sustainability</span><span>Resources</span><span>Competitors</span><span>Inquire</span>
  </nav>
</header>

<section class="abs hero" role="img" aria-label="Jet flying upward between tall towers under a night sky">
  <div class="abs shade"></div>
  <h1 class="abs">LUXURY IN THE SKIES</h1>
  <p class="abs">Soaring above expectations, Velorane invites you to experience luxury in the skies.Unlock the epitome of luxury with Velorane's fleet of exclusive aircraft.Elevate your journey with Velorane and indulge in unparalleled luxury aloft.</p>
  <div class="abs btn btn-accent">Begin your tour</div>
</section>

<h2 class="abs intro-title">Luxury of Private Jet Travel with Fractional Ownership</h2>
<p class="abs intro-sub">Enjoy Hassle-Free Access and Flexibility, Tailored to Your Needs</p>
<svg class="abs chevron" width="52" height="52" viewBox="0 0 52 52"><circle cx="26" cy="26" r="26" fill="#fff"/><path d="M17 22 L26 31 L35 22" stroke="#000" stroke-width="3" fill="none" stroke-linecap="round" stroke-linejoin="round"/></svg>

<div class="abs feature" style="left:215px">
  <svg width="34" height="34" viewBox="0 0 34 34"><circle cx="17" cy="17" r="14" fill="none" stroke="#fff" stroke-width="2"/><circle cx="17" cy="17" r="9" fill="#fff"/><text x="17" y="21" font-size="11" font-weight="700" text-anchor="middle" fill="#000" font-family="Montserrat">$</text></svg>
  <p>Fractional ownership offers private jet benefits without full ownership costs, ideal for frequent flyers.</p>
  <div class="label">Cost effective</div>
</div>
<div class="abs feature" style="left:408px">
  <svg width="34" height="34" viewBox="0 0 34 34"><circle cx="17" cy="5" r="3" fill="#fff"/><path d="M6 11 H28 M17 11 V21 M17 21 L11 32 M17 21 L23 32" stroke="#fff" stroke-width="3" stroke-linecap="round" fill="none"/></svg>
  <p>Gain reliable access to a fleet of private aircraft for convenient travel.</p>
  <div class="label">Accessibility</div>
</div>
<div class="abs feature" style="left:600px">
  <svg width="34" height="34" viewBox="0 0 34 34"><circle cx="17" cy="9" r="5" fill="none" stroke="#fff" stroke-width="3"/><circle cx="8" cy="25" r="5" fill="none" stroke="#fff" stroke-width="3"/><circle cx="26" cy="25" r="5" fill="none" stroke="#fff" stroke-width="3"/></svg>
  <p>Tailor your ownership share to match your travel needs and budget precisely.</p>
  <div class="label">Customisation</div>
</div>
<div class="abs feature" style="left:794px">
  <svg width="34" height="34" viewBox="0 0 34 34"><rect x="3" y="22" width="4" height="10" fill="#fff"/><rect x="9" y="17" width="4" height="15" fill="#fff"/><rect x="15" y="10" width="4" height="22" fill="#fff"/><path d="M17 2 L11 9 H23 Z" fill="#fff"/><circle cx="26" cy="22" r="7" fill="none" stroke="#fff" stroke-width="2"/><text x="26" y="26" font-size="10" font-weight="700" text-anchor="middle" fill="#fff" font-family="Montserrat">$</text></svg>
  <p>Enjoy potential asset value increase and tax advantages with fractional ownership.</p>
  <div class="label">Profitable</div>
</div>

<section class="redefine">
  <h2 class="abs">Re-defining Aviation luxury</h2>
  <p class="abs">Unlock unparalleled convenience, &nbsp;opulence and personalised service with &nbsp;Velorane's premier selection of exclusive &nbsp;aviation programs, tailored to elevate &nbsp;your travel experience to new heights.</p>
  <div class="abs btn btn-accent">Available programs</div>
</section>
<div class="abs redefine-photo" role="img" aria-label="Hand holding a model airliner against a sunlit city skyline"></div>

<section class="abs journey" role="img" aria-label="Aircraft wing above clouds at dusk">
  <h2 class="abs">ELEVATE YOUR JOURNEY</h2>
  <div class="abs tagline">Unparalleled Experience | Luxurious Comfront | Personalised Service</div>
  <p class="abs">Whether you're traveling for business or pleasure, Velorane is dedicated to provide with the highest level of service and comfort. Experience the difference with Velorane and elevate your travel experience to new heights.</p>
  <div class="abs service" style="left:362px">
    <svg width="26" height="24" viewBox="0 0 26 24"><rect x="2" y="3" width="18" height="18" rx="2" fill="#fff"/><circle cx="19" cy="17" r="6" fill="#3a3a3e" stroke="#fff" stroke-width="2"/><path d="M19 14 V17 H21" stroke="#fff" stroke-width="1.5" fill="none"/></svg>
    ON-DEMAND CHARTER
  </div>
  <div class="abs service" style="left:520px">
    <svg width="26" height="24" viewBox="0 0 26 24"><path d="M16 2 V10 M12 6 H20" stroke="#fff" stroke-width="3"/><path d="M2 14 H10 L16 17 H22 L22 20 L12 22 H2 Z" fill="#fff"/></svg>
    GLOBAL MEDICAL RESPONSE
  </div>
  <div class="abs service" style="left:677px">
    <svg width="26" height="24" viewBox="0 0 26 24"><circle cx="13" cy="12" r="10" fill="none" stroke="#fff" stroke-width="2"/><circle cx="13" cy="10" r="3" fill="#fff"/><path d="M8 17 Q13 12 18 17" fill="#fff"/></svg>
    PERSONALISED SERVICES
  </div>
  <div class="abs cta">Ready to Soar? Contact Us Today for Your Personalised Consultation</div>
  <div class="abs btn btn-white">Book call now</div>
</section>

<section class="clients">
  <div class="abs world-map" role="img" aria-label="Dotted world map"></div>
  <h2 class="abs">DISCOVER OUR CLIENTS ARE SAYING</h2>
  <p class="abs lead">Explore Real Testimonials Highlighting the Excellence of Velorane's Service. Ready to Experience Luxury Travel? Book Your Journey Today!"</p>
  <div class="abs btn btn-accent">Book call now</div>
  <svg class="abs bubble" width="1200" height="2400" viewBox="0 0 1200 2400" style="left:0;top:0">
    <path d="M656 1975 Q660 1962 675 1961 L945 1951 Q968 1952 962 1972 L940 2080 Q934 2100 915 2100 L900 2100 L870 2124 L876 2100 L645 2100 Q625 2099 626 2080 Z"/>
    <circle class="ring" cx="671" cy="1983" r="20"/><circle class="ring-in" cx="671" cy="1983" r="17"/>
    <text x="671" y="1995" font-size="30" font-weight="700" text-anchor="middle" fill="#fff" font-family="Montserrat">“</text>
    <path d="M300 2158 Q297 2142 315 2142 L615 2150 Q637 2150 637 2172 L637 2275 Q637 2292 620 2292 L394 2292 L394 2316 L367 2292 L340 2292 Q325 2292 322 2277 Z"/>
    <circle class="ring" cx="591" cy="2173" r="20"/><circle class="ring-in" cx="591" cy="2173" r="17"/>
    <text x="591" y="2189" font-size="30" font-weight="700" text-anchor="middle" fill="#fff" font-family="Montserrat">”</text>
  </svg>
  <p class="abs quote-text">Velorane sets the standard for luxury travel. Impeccable service from booking to landing &nbsp;- Claire M.</p>
</section>

<div class="abs partners" style="left:215px">Aerovance</div>
<div class="abs partners" style="left:410px">Skyloom</div>
<div class="abs partners" style="left:604px">Corvanta</div>
<div class="abs partners" style="left:798px">Altiprise</div>

<footer class="abs footer">
  <div class="abs logo">Velorane<span class="mark"></span></div>
  <p class="abs tag">Redefining Luxury Travel with Convenience, Opulence, and personalised Service, elevate Your Journey with us.</p>
  <nav class="abs nav">
    <span>Aircraft</span><span>Programs</span><span>Why velorane</span><span>Lifestyle</span><span>Sustainability</span><span>Resources</span><span>Competitors</span><span>Inquire</span>
  </nav>
  <div class="abs rule"></div>
  <h3 class="abs">CONTACT US</h3>
</footer>

<div class="abs contact" style="top:2800px">
  <svg width="14" height="10" viewBox="0 0 14 10"><rect width="14" height="10" fill="#fff"/><path d="M0 0 L7 6 L14 0" stroke="#141415" stroke-width="1.2" fill="none"/></svg>
  <div>info@velorane.com<br>mailto:info@velorane.com</div>
</div>
<div class="abs contact" style="top:2855px">
  <svg width="14" height="14" viewBox="0 0 14 14"><circle cx="7" cy="7" r="7" fill="#fff"/><path d="M4 4 Q4 10 10 10 L10 8.5 L8.5 8 L7.8 8.8 Q5.5 8 5.2 6.2 L6 5.5 L5.5 4 Z" fill="#141415"/></svg>
  <div>800-555-0142</div>
</div>
<div class="abs contact" style="top:2892px">
  <svg width="12" height="15" viewBox="0 0 12 15"><path d="M6 0 A6 6 0 0 1 12 6 Q12 10 6 15 Q0 10 0 6 A6 6 0 0 1 6 0Z" fill="#fff"/><circle cx="6" cy="6" r="2.3" fill="#141415"/></svg>
  <div>2210 Harbor Crest Ave, Suite 4<br>Marlow Bay, Florida 33980</div>
</div>

<div class="abs social" style="left:705px"></div>
<div class="abs social" style="left:737px"></div>
<div class="abs social" style="left:769px"></div>
<p class="abs newsletter">Stay Updated with Exclusive Offers and Industry News. Subscribe to Our Newsletter Today !</p>
<div class="abs email-input">enter your email</div>
<div class="abs subscribe">SUBSCRIBE NOW</div>

<div class="abs legal" style="left:215px">© 2024 Velorane. All rights reserved</div>
<div class="abs legal" style="left:811px">Terms of Use | Privacy Policy</div>

</body>
</html>
```